ambitious event and festival agency from austria needs fresh business card design

A new design is due for the new headquarters and the new challenges. We organize events for different target groups from 16 to 60 years. The design should therefore be straightforward and not confused, so we are open to new colors and the logo may also be changed. In general, however, the most interesting suggestions are the most interesting ones. after this order we are looking for more graphics for brightloom facebook instagramm homepage etc A new design is due for the new headquarters and the new challenges. We organize events for different target groups from 16 to 60 years. The design should therefore be straightforward and not confused, so we are open to new colors and the logo may also be changed. In general, however, the most interesting suggestions are the most interesting ones. after this order we are looking for more graphics for brightloom facebook instagramm homepage etc A new design is due for the new headquarters and the new challenges. We organize events for different target groups from 16 to 60 years. The design should therefore be straightforward and not confused, so we are open to new colors and the logo may also be changed. In general, however, the most interesting suggestions are the most interesting ones. after this order we are looking for more graphics for brightloom facebook instagramm homepage etc
Updates

Reason: I am sorry for this decision but i need some more time. No new designs please, there are so many good ones and I will have made a decision in the next 3 days.

Target Market(s)

Industry/Entity Type

Business

Font styles to use
Serif
Sans Serif

Colors

Designer to choose colors to be used in the design.

Requirements
Must have
Nice to have
Should not have

```html
<!DOCTYPE html>
<html lang="de">
<head>
<meta charset="utf-8">
<title>brightloom – Visitenkarte</title>
<link rel="stylesheet" href="https://fonts.googleapis.com/css2?family=Open+Sans:wght@400;600;700&display=swap">
<style>
  :root {
    --brand-red: #c8283f;
    --swoosh-grey: #7d8486;
    --card-white: #f6f6f4;
    --text-grey: #6f7375;
    --back-grey-light: #8a9193;
    --back-grey-dark: #5c6365;
    --back-text: #c9cdce;
    --stage: #e9e7e3;
  }
  * { box-sizing: border-box; margin: 0; padding: 0; }
  html, body {
    width: 1200px; height: 780px; overflow: hidden;
    background: var(--stage);
    font-family: "Open Sans", Arial, sans-serif;
  }
  .sheet {
    position: relative; width: 1200px; height: 780px;
    display: flex; align-items: center; justify-content: center; gap: 40px;
  }
  .card {
    position: relative; width: 540px; height: 309px;
    border-radius: 18px; overflow: hidden;
    box-shadow: 0 10px 28px rgba(0,0,0,.18);
  }
  /* front */
  .card--front { background: var(--card-white); }
  .card__band { position: absolute; inset: 0; width: 100%; height: 100%; }
  .card__holder {
    position: absolute; top: 18px; right: 26px; text-align: right; color: #fff;
  }
  .card__holder-name { font-size: 17px; font-weight: 600; letter-spacing: .2px; }
  .card__holder-role { font-size: 12px; font-weight: 400; margin-top: 1px; }
  .wordmark {
    font-weight: 700; letter-spacing: -1px; line-height: 1;
    color: var(--brand-red);
  }
  .card--front .wordmark {
    position: absolute; left: 60px; top: 134px; font-size: 52px;
    display: flex; align-items: center; gap: 10px;
  }
  .wordmark__dot {
    width: 12px; height: 12px; background: var(--brand-red); flex: none;
  }
  .contact {
    position: absolute; left: 82px; top: 204px;
    color: var(--text-grey); font-size: 11.5px; line-height: 15px;
  }
  .contact__company { font-weight: 600; }
  .contact__details { display: flex; gap: 8px; margin-top: 2px; }
  .contact__icons { display: flex; gap: 3px; align-self: flex-end; margin-left: -22px; margin-bottom: 1px; }
  .contact__icon { width: 16px; height: 16px; flex: none; }
  /* back */
  .card--back {
    background: radial-gradient(ellipse at 45% 40%, var(--back-grey-light), var(--back-grey-dark));
  }
  .card--back .wordmark {
    position: absolute; left: 0; right: 0; top: 118px;
    font-size: 64px; display: flex; justify-content: center; align-items: center; gap: 12px;
  }
  .card--back .wordmark__dot { width: 14px; height: 14px; }
  .card__web {
    position: absolute; left: 0; right: 0; top: 206px; text-align: center;
    font-size: 13px; letter-spacing: 1px; color: var(--back-text);
  }
</style>
</head>
<body>
<main class="sheet">
  <section class="card card--front" aria-label="Vorderseite">
    <svg class="card__band" viewBox="0 0 540 309" preserveAspectRatio="none" aria-hidden="true">
      <path d="M0 0 H540 V96 C400 40 190 30 0 96 Z" fill="var(--brand-red)"/>
      <path d="M0 104 C190 40 400 50 540 100 V108 C400 60 190 52 0 112 Z" fill="var(--swoosh-grey)"/>
    </svg>
    <div class="card__holder">
      <div class="card__holder-name">Markus Weidinger</div>
      <div class="card__holder-role">Geschäftsführer</div>
    </div>
    <div class="wordmark"><span class="wordmark__dot"></span>brightloom</div>
    <div class="contact">
      <div class="contact__company">brightloom</div>
      <div>Talgasse 12, A6210 Bergfeld</div>
      <div class="contact__details">
        <div class="contact__icons" style="flex-direction:column;gap:0;margin-left:-24px;">
          <svg class="contact__icon" viewBox="0 0 16 16" aria-label="Telefon" style="height:15px"><rect width="15" height="13" y="1" rx="3" fill="var(--brand-red)"/><rect x="5" y="3.5" width="5" height="8" rx="1" fill="none" stroke="#fff" stroke-width="1.2"/></svg>
          <svg class="contact__icon" viewBox="0 0 16 16" aria-label="E-Mail" style="height:15px"><rect width="15" height="13" y="1" rx="3" fill="var(--brand-red)"/><rect x="3" y="4.5" width="9" height="6" fill="none" stroke="#fff" stroke-width="1.1"/><path d="M3 4.5 L7.5 8 L12 4.5" fill="none" stroke="#fff" stroke-width="1.1"/></svg>
          <svg class="contact__icon" viewBox="0 0 16 16" aria-label="Web" style="height:15px"><rect width="15" height="13" y="1" rx="3" fill="var(--brand-red)"/><circle cx="7.5" cy="7.5" r="4" fill="none" stroke="#fff" stroke-width="1.1"/><path d="M3.5 7.5 H11.5 M7.5 3.5 V11.5" stroke="#fff" stroke-width="1"/></svg>
        </div>
        <div class="contact__lines">
          <div>+43 660 418 2730</div>
          <div>m.weidinger@brightloom.eu</div>
          <div>www.brightloom.eu</div>
        </div>
      </div>
    </div>
  </section>

  <section class="card card--back" aria-label="Rückseite">
    <div class="wordmark"><span class="wordmark__dot"></span>brightloom</div>
    <div class="card__web">www.brightloom.eu</div>
  </section>
</main>
</body>
</html>
```